Business Management Fortress

Assist with enhancing a powerpoint slide by providing a few design options for consideration. I have a template but open to any creative ideas.

Internal employees and stakeholders

Business Management, Finance, Accounting

• Maintain a fortress, temple, or pyramid schema
• Scenic Background

```html
<!DOCTYPE html>
<html lang="en">
<head>
<meta charset="UTF-8">
<title>Business Management Fortress</title>
<link href="https://fonts.googleapis.com/css2?family=Roboto:wght@400;500&display=swap" rel="stylesheet">
<style>
  :root {
    --brown: #8c6c5f;
    --brown-dark: #6f5247;
    --panel: #e3e5e9;
    --ink: #111111;
    --white: #ffffff;

    --yellow: #f3ba1c;
    --yellow-deep: #8a6b0b;
    --yellow-mid: #f5cf6a;
    --yellow-soft: #f6ead0;

    --red: #ec1c24;
    --red-deep: #8c0f16;
    --red-mid: #ee2229;
    --red-soft: #f4a9ae;

    --green: #8dc63f;
    --green-deep: #4a781d;
    --green-mid: #8fc84a;
    --green-soft: #cce7a3;

    --blue: #58a6de;
    --blue-deep: #336d9d;
    --blue-mid: #6198c4;
    --blue-soft: #a9d0ee;
  }
  * { box-sizing: border-box; margin: 0; padding: 0; }
  html, body { width: 1200px; height: 675px; overflow: hidden; }
  body { font-family: 'Roboto', sans-serif; }

  .slide { position: relative; width: 1200px; height: 675px; overflow: hidden; }

  .scenic-backdrop {
    position: absolute; inset: 0;
    background:
      radial-gradient(ellipse at 15% 20%, rgba(247,214,160,0.85), rgba(247,214,160,0) 55%),
      radial-gradient(ellipse at 85% 30%, rgba(214,196,178,0.8), rgba(214,196,178,0) 60%),
      linear-gradient(180deg, #eee6da 0%, #ebe1d2 45%, #e4d8c6 75%, #ddd1bf 100%);
  }

  .temple-panel {
    position: absolute; left: 160px; top: 129px; width: 880px; height: 341px;
    background: var(--panel);
  }

  .roof { position: absolute; left: 0; top: 0; width: 1200px; height: 160px; }

  .roof-label {
    position: absolute; top: 165px; font-size: 22px; font-weight: 400; color: var(--ink);
    transform: translateX(-50%); white-space: nowrap;
  }

  .pillar { position: absolute; top: 129px; width: 184px; height: 341px; transform: translateX(-50%); }
  .pillar > div { position: absolute; left: 50%; transform: translateX(-50%); }
  .cap-outer { width: 109px; height: 21px; }
  .cap-inner { width: 81px; height: 14px; }
  .shaft { width: 61px; }
  .cap-top.cap-outer { top: 0; }
  .cap-top.cap-inner { top: 21px; }
  .shaft-top { top: 35px; height: 44px; }
  .shaft-bottom { top: 268px; height: 39px; }
  .cap-bottom.cap-inner { top: 307px; }
  .cap-bottom.cap-outer { top: 320px; }

  .pillar-body {
    top: 79px; width: 184px; height: 189px; border-radius: 8px;
    display: flex; align-items: center; justify-content: center; text-align: center;
    color: var(--white); font-size: 25px; font-weight: 500; line-height: 1.35;
  }
  .pillar-number {
    top: 50px; width: 60px; height: 60px; border-radius: 50%;
    display: flex; align-items: center; justify-content: center;
    color: var(--white); font-size: 22px; font-weight: 500; border: 3px solid;
  }

  .pillar--people .cap-outer { background: var(--yellow); }
  .pillar--people .cap-inner { background: var(--yellow-mid); }
  .pillar--people .shaft { background: var(--yellow-soft); }
  .pillar--people .pillar-body { background: var(--yellow); box-shadow: 0 3px 0 #a97e0c; }
  .pillar--people .pillar-number { background: var(--yellow-deep); border-color: #f7d36b; }

  .pillar--innovation .cap-outer { background: var(--red-deep); }
  .pillar--innovation .cap-inner { background: var(--red-mid); }
  .pillar--innovation .shaft { background: var(--red-soft); }
  .pillar--innovation .pillar-body { background: var(--red); box-shadow: 0 3px 0 #9a0f16; }
  .pillar--innovation .pillar-number { background: var(--red-deep); border-color: #f26a70; }

  .pillar--intelligence .cap-outer { background: var(--green-deep); }
  .pillar--intelligence .cap-inner { background: var(--green-mid); }
  .pillar--intelligence .shaft { background: var(--green-soft); }
  .pillar--intelligence .pillar-body { background: var(--green); box-shadow: 0 3px 0 #4e7d20; }
  .pillar--intelligence .pillar-number { background: var(--green-deep); border-color: #a8d86a; }

  .pillar--alliances .cap-outer { background: var(--blue-deep); }
  .pillar--alliances .cap-inner { background: var(--blue-mid); }
  .pillar--alliances .shaft { background: var(--blue-soft); }
  .pillar--alliances .pillar-body { background: var(--blue); box-shadow: 0 3px 0 #2e6592; }
  .pillar--alliances .pillar-number { background: var(--blue-deep); border-color: #7db8e6; }

  .foundation {
    position: absolute; left: 137px; top: 470px; width: 924px; height: 47px;
    background: var(--brown); border-radius: 0 0 6px 6px;
    box-shadow: 0 2px 0 var(--brown-dark);
    display: flex; align-items: center; justify-content: center;
    color: var(--white); font-size: 22px; font-weight: 500;
  }

  .foundation-note {
    position: absolute; left: 300px; top: 548px; width: 600px;
    text-align: center; font-size: 27px; font-weight: 400; line-height: 38px; color: var(--ink);
  }
</style>
</head>
<body>
  <main class="slide">
    <div class="scenic-backdrop" role="img" aria-label="Soft, sunlit scene of ancient temple ruins behind the diagram"></div>

    <div class="temple-panel"></div>

    <svg class="roof" viewBox="0 0 1200 160" aria-hidden="true">
      <path d="M150 103 L600 51 L1050 103 Z" fill="var(--brown)"/>
      <rect x="139" y="103" width="923" height="26" rx="13" fill="var(--brown-dark)"/>
      <g fill="var(--brown-dark)" stroke="var(--white)" stroke-width="5">
        <rect x="352" y="107" width="28" height="28" transform="rotate(45 366 121)"/>
        <rect x="586" y="107" width="28" height="28" transform="rotate(45 600 121)"/>
        <rect x="822" y="107" width="28" height="28" transform="rotate(45 836 121)"/>
      </g>
    </svg>

    <span class="roof-label" style="left:366px">Leader</span>
    <span class="roof-label" style="left:600px">Partner</span>
    <span class="roof-label" style="left:839px">Profitability</span>

    <section class="pillar pillar--people" style="left:252px">
      <div class="cap-outer cap-top"></div><div class="cap-inner cap-top"></div>
      <div class="shaft shaft-top"></div>
      <div class="pillar-body">People</div>
      <div class="pillar-number">1</div>
      <div class="shaft shaft-bottom"></div>
      <div class="cap-inner cap-bottom"></div><div class="cap-outer cap-bottom"></div>
    </section>

    <section class="pillar pillar--innovation" style="left:484px">
      <div class="cap-outer cap-top"></div><div class="cap-inner cap-top"></div>
      <div class="shaft shaft-top"></div>
      <div class="pillar-body">Innovation</div>
      <div class="pillar-number">2</div>
      <div class="shaft shaft-bottom"></div>
      <div class="cap-inner cap-bottom"></div><div class="cap-outer cap-bottom"></div>
    </section>

    <section class="pillar pillar--intelligence" style="left:717px">
      <div class="cap-outer cap-top"></div><div class="cap-inner cap-top"></div>
      <div class="shaft shaft-top"></div>
      <div class="pillar-body">Business<br>Intelligence</div>
      <div class="pillar-number">3</div>
      <div class="shaft shaft-bottom"></div>
      <div class="cap-inner cap-bottom"></div><div class="cap-outer cap-bottom"></div>
    </section>

    <section class="pillar pillar--alliances" style="left:950px">
      <div class="cap-outer cap-top"></div><div class="cap-inner cap-top"></div>
      <div class="shaft shaft-top"></div>
      <div class="pillar-body">Alliances<br>Strategic</div>
      <div class="pillar-number">4</div>
      <div class="shaft shaft-bottom"></div>
      <div class="cap-inner cap-bottom"></div><div class="cap-outer cap-bottom"></div>
    </section>

    <div class="foundation">Fiduciary Responsibilities</div>

    <p class="foundation-note">Accurate Financials / Internal Controls / Brand Protection</p>
  </main>
</body>
</html>
```